Building company buisness cards

We are looking for a sharp modern new look for our business cards.We are a New Zealand based company that specialises in house and land packages.We have attached a photo of the current logo and would like to see if it can be improved somehow if needed.We are open to any colours but we have chosen Black and White at this stage. Feel free to change the font and make the logo smarter looking.Play with the colours and see what looks best.We want a card that looks so good know one will want to throw it away!

Target Market(s)

Building profesonals, home buyers

Industry/Entity Type

Building

Contact Information for Business Card

Garrick Tenwood
0275390628
garrickt@hartvale.co.nz

Font styles to use
Serif
Sans Serif

Colors

Designer to choose colors to be used in the design.

Requirements
Must have
• Just the logo on one side and details on the other
• Clean simple looking card
Nice to have
• Round corners and detail like raised or spot UV
• Something that stands out
Should not have
• To title needed, Director etc

```html
<!DOCTYPE html>
<html lang="en">
<head>
<meta charset="utf-8">
<title>Hartvale business cards</title>
<link rel="stylesheet" href="https://fonts.googleapis.com/css2?family=Open+Sans:wght@400;700&display=swap">
<style>
  :root {
    --backdrop: #e9e6e1;
    --card-edge: #14151a;
    --card-face: #ffffff;
    --ink: #111111;
    --ink-soft: #3a3a3a;
    --rule: #cfcfcf;
  }
  * { box-sizing: border-box; margin: 0; padding: 0; }
  html, body {
    width: 1200px; height: 885px; overflow: hidden;
    background: var(--backdrop);
  }
  .sheet {
    width: 1200px; height: 885px;
    display: flex; flex-direction: column; align-items: center; justify-content: center;
    gap: 56px;
  }
  .card {
    width: 640px; height: 366px;
    background: var(--card-edge);
    border-radius: 26px;
    padding: 9px;
    box-shadow: 0 14px 30px rgba(0,0,0,0.18);
  }
  .card-face {
    width: 100%; height: 100%;
    background: var(--card-face);
    border-radius: 19px;
    position: relative;
  }

  .brand-name {
    font-family: "Open Sans", Arial, sans-serif;
    font-weight: 700; color: var(--ink);
    line-height: 1;
  }

  /* logo side */
  .card-face--logo {
    display: flex; flex-direction: column; align-items: center; justify-content: center;
    gap: 44px;
  }
  .brand-name--large { font-size: 54px; }
  .website-spaced {
    font-family: "Open Sans", Arial, sans-serif;
    font-size: 13px; letter-spacing: 0.55em; color: var(--ink-soft);
  }

  /* details side */
  .card-face--details {
    display: flex; align-items: center;
  }
  .details-brand {
    width: 360px; display: flex; justify-content: center; align-items: center;
    padding-top: 90px;
  }
  .brand-name--medium { font-size: 46px; }
  .divider {
    width: 1px; height: 150px; background: var(--rule); margin-top: -40px;
  }
  .contact {
    padding-left: 30px; margin-top: -40px;
    font-family: "Open Sans", Arial, sans-serif; color: var(--ink-soft);
  }
  .contact-name {
    font-weight: 700; font-size: 20px; color: var(--ink); margin-bottom: 10px;
  }
  .contact-list { list-style: none; font-size: 14px; line-height: 1.55; }
  .contact-list li { display: flex; align-items: center; gap: 9px; }
  .contact-list svg { width: 13px; height: 13px; flex: none; fill: var(--ink); }
</style>
</head>
<body>
<main class="sheet">
  <section class="card card--front" aria-label="Card front">
    <div class="card-face card-face--logo">
      <p class="brand-name brand-name--large">Hartvale</p>
      <p class="website-spaced">www.hartvale.co.nz</p>
    </div>
  </section>

  <section class="card card--back" aria-label="Card back">
    <div class="card-face card-face--details">
      <div class="details-brand">
        <p class="brand-name brand-name--medium">Hartvale</p>
      </div>
      <div class="divider"></div>
      <div class="contact">
        <p class="contact-name">Garrick Tenwood</p>
        <ul class="contact-list">
          <li>
            <svg viewBox="0 0 16 16" aria-hidden="true"><path d="M3 1.5l2.6 2.8-1.3 2a9 9 0 0 0 5.4 5.4l2-1.3 2.8 2.6-1.6 1.8C7.5 14.6 1.4 8.5 1.2 3.1z"/></svg>
            <span>0275390628</span>
          </li>
          <li>
            <svg viewBox="0 0 16 16" aria-hidden="true"><path d="M1 3h14v10H1z M2.5 4.5L8 9l5.5-4.5" fill="none" stroke="#111" stroke-width="1.6"/></svg>
            <span>garrickt@hartvale.co.nz</span>
          </li>
          <li>
            <svg viewBox="0 0 16 16" aria-hidden="true"><circle cx="8" cy="8" r="6.8" fill="none" stroke="#111" stroke-width="1.4"/><path d="M1.5 8h13M8 1.2c-3 3.5-3 10 0 13.6M8 1.2c3 3.5 3 10 0 13.6" fill="none" stroke="#111" stroke-width="1.2"/></svg>
            <span>www.hartvale.co.nz</span>
          </li>
        </ul>
      </div>
    </div>
  </section>
</main>
</body>
</html>
```